Business cards for Norwegian software consultancy business

We are in need of business cards for our Norwegian consultancy company.
“Valto Brindex AS” specializes in software development, architecture and agile methodology, providing mostly on-site services at customers.
The cards should reflect a certain level of business professionalism with an elegant touch, while paying tribute to our modern and technological heritage. Our logo should be featured, as well as room for basic information about the cardholder and legal information of the company (company name, address and VAT number).
We would like our cards to reflect that we are a modern consulting company. It should present a professional image that people will remember. The texture and color pallette should reflect our professionalism and reliability, so we prefer a light color pallette with colors such as gray, white, blue and black. The number of colors used should however not be overwhelming, with the text being distinct and readable.
We are open to untraditional layouts and playful designs as long as they communicate the intent stated above.
You could also take a look at our website http://www.brindex.no for input on our visual profile.
Our logo is attached in the form of vectors and rasterized PNG. Please comment if you would like the black-white and/or inverted versions as well.
Industry/Entity Type
Architecture
Contact Information for Business Card
Company information:
Valto Brindex AS
Kvernlia 14, 3170 Sem
482 71 519
info@brindex.no
www.brindex.no
Employee information:
Full name
Title
Email
Phone
Font styles to use
Look and feel

```html
<!DOCTYPE html>
<html lang="no">
<head>
<meta charset="utf-8">
<title>Valto Brindex AS – Business Cards</title>
<link href="https://fonts.googleapis.com/css2?family=Lato:wght@400;700&display=swap" rel="stylesheet">
<style>
  :root {
    --backdrop: #cfcecc;
    --ink-dark: #222322;
    --paper: #f4f4f3;
    --text-dark: #262626;
    --text-light: #ffffff;
    --accent-blue: #4f86b8;
    --faint-mark: #e6e6e5;
    --faint-mark-dark: #2b2c2b;
  }
  * { margin: 0; padding: 0; box-sizing: border-box; }
  html, body { width: 1200px; height: 900px; overflow: hidden; }
  body {
    background: var(--backdrop);
    font-family: "Lato", Arial, sans-serif;
    position: relative;
  }
  .card {
    position: absolute;
    left: 340px;
    width: 520px;
    height: 290px;
    overflow: hidden;
    box-shadow: 0 2px 6px rgba(0,0,0,0.18);
  }
  .card--front { top: 120px; background: var(--ink-dark); color: var(--text-light); }
  .card--back { top: 470px; background: var(--paper); color: var(--text-dark); }

  .faint-block {
    position: absolute;
    width: 250px; height: 230px;
    left: 250px; top: 40px;
    border: 28px solid var(--faint-mark-dark);
  }
  .card--back .faint-block { border-color: var(--faint-mark); left: 270px; top: 70px; }

  .brand {
    position: absolute;
    display: flex;
    align-items: center;
    gap: 10px;
  }
  .brand__square { width: 30px; height: 30px; background: currentColor; }
  .brand__name {
    font-size: 25px;
    font-weight: 400;
    letter-spacing: 2px;
    line-height: 1;
  }
  .card--front .brand { left: 130px; top: 128px; }
  .card--back .brand { right: 26px; top: 38px; }
  .card--back .brand__square { background: var(--accent-blue); }

  .web {
    position: absolute;
    font-size: 13px;
    letter-spacing: 2.5px;
  }
  .card--front .web { left: 190px; bottom: 28px; display: flex; align-items: center; gap: 10px; }
  .web__arrow { width: 0; height: 0; border-left: 6px solid var(--text-light); border-top: 4px solid transparent; border-bottom: 4px solid transparent; }

  .company {
    position: absolute; left: 44px; top: 42px;
    font-size: 13px; line-height: 17px;
  }
  .company__name { font-weight: 700; }

  .contact {
    position: absolute; left: 56px; top: 148px;
    list-style: none; font-size: 13px; line-height: 17px;
  }
  .contact li { display: flex; align-items: center; gap: 9px; }
  .contact svg { width: 11px; height: 11px; fill: none; stroke: var(--accent-blue); stroke-width: 1.4; }

  .band { position: absolute; left: 0; bottom: 0; width: 520px; height: 80px; }
  .holder {
    position: absolute; left: 40px; bottom: 20px;
    color: var(--text-light); font-size: 16px;
  }
  .holder__title { font-size: 11px; letter-spacing: 0.5px; text-transform: uppercase; }
  .card--back .web { right: 36px; bottom: 46px; color: var(--text-light); }
</style>
</head>
<body>
  <section class="card card--front" aria-label="Card front">
    <div class="faint-block"></div>
    <div class="brand">
      <span class="brand__square"></span>
      <span class="brand__name">VALTO BRINDEX</span>
    </div>
    <p class="web"><span class="web__arrow"></span>www.brindex.no</p>
  </section>

  <section class="card card--back" aria-label="Card back">
    <div class="faint-block"></div>
    <div class="brand">
      <span class="brand__square"></span>
      <span class="brand__name">VALTO BRINDEX</span>
    </div>

    <address class="company" style="font-style:normal">
      <div class="company__name">Valto Brindex AS</div>
      <div>Kvernlia 14</div>
      <div>3170 Sem</div>
    </address>

    <ul class="contact">
      <li><svg viewBox="0 0 12 12"><path d="M2 1.5l2 0 1 2.5-1.3 1a6 6 0 0 0 3.3 3.3l1-1.3 2.5 1v2a1 1 0 0 1-1 1A9 9 0 0 1 1 2.5a1 1 0 0 1 1-1z"/></svg>482 71 519</li>
      <li><svg viewBox="0 0 12 12"><rect x="1" y="4.5" width="10" height="5"/><rect x="3" y="1" width="6" height="3.5"/><rect x="3" y="8" width="6" height="3"/></svg>482 71 520</li>
      <li><svg viewBox="0 0 12 12"><rect x="1" y="2.5" width="10" height="7"/><path d="M1 2.5l5 4 5-4"/></svg>eholm@brindex.no</li>
    </ul>

    <svg class="band" viewBox="0 0 520 80" aria-hidden="true">
      <path d="M0 14 H30 L36 6 L42 14 H520 V80 H0 Z" fill="var(--ink-dark)"/>
    </svg>
    <p class="holder">Eirik Holm <span style="opacity:.8">|</span> <span class="holder__title">Director</span></p>
    <p class="web">www.brindex.no</p>
  </section>
</body>
</html>
```